New Business Card Design for Manufacturing

We are an engineering/manufacturing company that offers Advanced machining/assembly/engineering services, as well as innovative products for the heavy duty engine cooling markets.

We are looking to get a new business card designed that is clean and modern looking, but still fits the wide range of technical/skilled work we do.

- We hope to use this design as the base for other design work in new Presentations, web, and print work.

Industry/Entity Type

Engineering

Contact Information for Business Card

Our preferred color of blue is (RGB) 22/71/159 but can vary slightly from that color. Our content will be our Logo and full company name (Vantrell Forge Works, Inc.), company address, name, job title, phone number with extension, cell number, fax number, website, and email address on the cards.
We'd like the full company name next to the logo, but we are open to other interpretations of that layout.
Preferably, we would like the back side to be clean with just our logo, and the front to contain all of the contact information.

Colors
2f74b4
0355a3
85abd2

Requirements
Must have
• - Logo, company name, needed content - We are open to interpretation beyond that.
• - Standard size business card.
• - Horizontal orientation.
• - Enough space for lengthy names / job titles (for example, a job title could read "Directory of Human Resources" or "V.P. of Governmental Affairs"). We need this to look clean, whether the title be short (CEO) or long (as described above).

```html
<!DOCTYPE html>
<html lang="en">
<head>
<meta charset="utf-8">
<title>Vantrell Forge Works – Business Card</title>
<link rel="stylesheet" href="https://fonts.googleapis.com/css2?family=Open+Sans:wght@400;600;800&family=Fira+Sans:wght@500&family=Quicksand:wght@700&display=swap">
<style>
  :root {
    --brand-blue: #0355a3;
    --brand-blue-mid: #2f74b4;
    --brand-blue-light: #85abd2;
    --card-black: #0b0b0c;
    --card-white: #f7f7f7;
    --ink-white: #ffffff;
    --backdrop: #e4e4e4;
  }
  * { margin: 0; padding: 0; box-sizing: border-box; }
  html, body { width: 1200px; height: 576px; overflow: hidden; }
  body {
    position: relative;
    background: var(--backdrop);
    font-family: "Open Sans", Arial, sans-serif;
  }
  .card {
    position: absolute;
    top: 138px;
    height: 293px;
    border-radius: 12px;
    overflow: hidden;
  }
  .card-back {
    left: 82px;
    width: 485px;
    background: var(--card-black);
  }
  .card-front {
    left: 602px;
    width: 481px;
    background: var(--card-white);
  }
  .wordmark {
    position: absolute;
    font-family: "Open Sans", Arial, sans-serif;
    font-weight: 800;
    letter-spacing: 1px;
    white-space: nowrap;
    transform: translateX(-50%);
  }
  .card-back .wordmark {
    left: 50%;
    top: 112px;
    font-size: 50px;
    color: var(--ink-white);
  }
  .card-front .wordmark {
    left: 50%;
    top: 30px;
    font-size: 40px;
    color: var(--brand-blue);
  }
  .contact-band {
    position: absolute;
    left: 0;
    top: 120px;
    width: 100%;
    height: 132px;
    background: var(--brand-blue);
    color: var(--ink-white);
  }
  .holder-name {
    position: absolute;
    left: 26px;
    top: 8px;
    font-family: "Fira Sans", Arial, sans-serif;
    font-weight: 500;
    font-size: 19px;
  }
  .holder-title {
    position: absolute;
    left: 26px;
    top: 33px;
    font-size: 11px;
  }
  .phone-list, .web-list {
    position: absolute;
    list-style: none;
    font-size: 11.5px;
    line-height: 16.5px;
  }
  .phone-list { left: 26px; top: 80px; }
  .web-list { right: 26px; top: 64px; text-align: right; }
  .phone-list li, .web-list li {
    display: flex;
    align-items: center;
    gap: 8px;
  }
  .web-list li { justify-content: flex-end; }
  .icon { width: 10px; height: 10px; flex: none; fill: var(--ink-white); }
  .company-name {
    position: absolute;
    left: 0;
    width: 100%;
    top: 261px;
    text-align: center;
    font-family: "Quicksand", Arial, sans-serif;
    font-weight: 700;
    font-size: 13.5px;
    color: var(--brand-blue);
  }
</style>
</head>
<body>

<section class="card card-back" aria-label="Card back">
  <div class="wordmark">VANTRELL</div>
</section>

<section class="card card-front" aria-label="Card front">
  <div class="wordmark">VANTRELL</div>

  <div class="contact-band">
    <div class="holder-name">John Doe Smith</div>
    <div class="holder-title">Managing Director</div>

    <ul class="phone-list">
      <li>
        <svg class="icon" viewBox="0 0 10 10"><path d="M1 3 Q5 0 9 3 L8 4.5 L6.5 3.5 L3.5 3.5 L2 4.5 Z M2 5 H8 V9 H2 Z"/></svg>
        111-2222-2222 (EXT)
      </li>
      <li>
        <svg class="icon" viewBox="0 0 10 10"><path d="M3 0 H7 Q8 0 8 1 V9 Q8 10 7 10 H3 Q2 10 2 9 V1 Q2 0 3 0 Z M3 1.5 V7.5 H7 V1.5 Z"/></svg>
        333-3333-3333
      </li>
      <li>
        <svg class="icon" viewBox="0 0 10 10"><path d="M2.5 0 H7.5 V3 H2.5 Z M0 3.5 H10 V7.5 H8 V6 H2 V7.5 H0 Z M2.5 6.5 H7.5 V10 H2.5 Z"/></svg>
        444-4444-4444
      </li>
    </ul>

    <ul class="web-list">
      <li>johndoe@yourwebsite.com
        <svg class="icon" viewBox="0 0 10 10"><path d="M0 2 H10 V8.5 H0 Z" /><path d="M0 2 L5 6 L10 2" fill="none" stroke="#0355a3" stroke-width="1"/></svg>
      </li>
      <li>www.yourwebsite.com
        <svg class="icon" viewBox="0 0 10 10"><circle cx="5" cy="5" r="4.5"/><path d="M0.5 5 H9.5 M5 0.5 V9.5 M1.5 2.8 H8.5 M1.5 7.2 H8.5" stroke="#0355a3" stroke-width="0.7" fill="none"/></svg>
      </li>
      <li>234 Anywhere St., Any City,
        <svg class="icon" viewBox="0 0 10 10"><path d="M5 0 A3.8 3.8 0 0 1 8.8 3.8 Q8.8 6 5 10 Q1.2 6 1.2 3.8 A3.8 3.8 0 0 1 5 0 Z"/><circle cx="5" cy="3.8" r="1.4" fill="#0355a3"/></svg>
      </li>
      <li style="padding-right:18px">Any Town, US 123456</li>
    </ul>
  </div>

  <div class="company-name">Vantrell Forge Works, Inc.</div>
</section>

</body>
</html>
```